Gospel Tract titled "A Lantern Trail Toward Bright Skies."

This will be a bi-fold brochure. The design will be in the front panel of the brochure which is 4 inches wide and 8.5 inches high. This is a common brochure among Gospel tracts in the series, "A lantern trail toward bright skies ______________ ." The blank is usually a state, city, or other location. I want a "fun" image of Iowa or something representing Iowa at the bottom. A graphic representing "heaven" at the top. Perhaps a meandering road between the two. The words, "A Lantern Trail Toward Bright Skies", but be on the front somewhere. I am also open to other designs with this theme and the words "A Lantern Trail Toward Bright Skies." My suggestion is just one idea.

Target Market(s)

Non-Christians who are interested in knowing how to get to heaven

Requirements
Must have
• Something specific to the state of Iowa at the bottom: farms, state fair, cows, barns, power windmills, the capitol building, etc.
Nice to have
• I would like something bright, colorful, with a fun Iowa image at the bottom.
Should not have
• Religous symbolism....no doves, angels, crosses, etc.

```html
<!DOCTYPE html>
<html lang="en">
<head>
<meta charset="utf-8">
<title>A Lantern Trail Toward Bright Skies From Iowa — Tract</title>
<link href="https://fonts.googleapis.com/css2?family=Archivo+Black&family=Montserrat:ital,wght@0,400;0,500;0,600;0,700;0,800;1,800&family=Allura&display=swap" rel="stylesheet">
<style>
:root{
  --page:#b9bfcf;
  --teal-dark:#15323d;
  --teal:#1d4a58;
  --teal-mid:#24596a;
  --gold:#d9b35c;
  --gold-deep:#b8913e;
  --ink-teal:#1b4657;
  --white:#ffffff;
  --pill-olive:rgba(150,146,96,.85);
  --pill-teal:rgba(38,126,136,.85);
  --pill-green:rgba(108,142,44,.9);
  --pill-slate:rgba(58,104,128,.85);
  --lbl-yellow:#f2e25a;
  --lbl-cyan:#5fe2ea;
  --lbl-lime:#b9f24a;
  --lbl-blue:#7fc9f2;
}
*{margin:0;padding:0;box-sizing:border-box}
html,body{width:1200px;height:2400px;overflow:hidden;background:var(--page)}
body{position:relative;font-family:'Montserrat',sans-serif;color:var(--white)}
.spread{position:absolute;left:73px;width:1054px;height:1120px;display:flex;box-shadow:0 6px 18px rgba(0,0,0,.25)}
.spread--outside{top:50px}
.spread--inside{top:1230px}
.panel{position:relative;height:100%;overflow:hidden}
.panel--back,.panel--way{width:532px;background:linear-gradient(180deg,var(--teal-mid) 0%,var(--teal) 45%,var(--teal-dark) 100%)}
.panel--cover{width:522px}
.panel--why{width:528px}
.panel--way{width:526px}
.abs{position:absolute;left:0;right:0;text-align:center}

/* back panel */
.journey-title{top:50px;font-family:'Archivo Black',sans-serif;color:var(--gold);font-size:46px;line-height:42px}
.journey-sub{top:148px;font-weight:800;font-size:27px;letter-spacing:3px}
.script{font-family:'Allura',cursive;color:#bcd9df;font-weight:400}
.congrats{top:186px;font-size:56px}
.lead{top:246px;font-size:15px;line-height:18px;color:#e6eef0}
.step{position:absolute;left:64px;width:406px;height:77px;border-radius:38px;text-align:center;padding-top:14px}
.step__label{font-weight:700;font-size:14px;letter-spacing:3px;display:block;margin-bottom:5px}
.step__text{font-size:14px;line-height:17px}
.step--bible{top:316px;background:var(--pill-olive)}
.step--bible .step__label{color:var(--lbl-yellow)}
.step--pray{top:402px;background:var(--pill-teal)}
.step--pray .step__label{color:var(--lbl-cyan)}
.step--church{top:488px;background:var(--pill-green)}
.step--church .step__label{color:var(--lbl-lime)}
.step--share{top:574px;background:var(--pill-slate)}
.step--share .step__label{color:var(--lbl-blue)}
.contact-intro{top:692px;font-size:15px;line-height:18px}
.contact-icons{top:746px;display:flex;justify-content:center;align-items:center;gap:8px}
.rule{width:48px;height:2px;background:#9bb3b9}
.icon-dot{width:24px;height:24px;border-radius:50%;background:#b9d46a;display:flex;align-items:center;justify-content:center}
.address{top:792px;font-size:15px;line-height:18px}
.phone{top:900px;font-size:15px}
.email{top:936px;font-size:15px}
.web{top:972px;font-size:15px}
.closing{top:1028px;font-size:15px;line-height:18px}
.qmark{font-family:'Archivo Black',sans-serif;position:absolute;line-height:1}
.closing .qmark{font-size:50px;color:#4c7f8e}

/* cover */
.cover-art{position:absolute;inset:0;background:
  radial-gradient(ellipse 30% 38% at 50% 26%,#fff7df 0%,#f4dcaa 30%,rgba(220,190,150,0) 70%),
  linear-gradient(180deg,#c6a27e 0%,#8f8aa0 30%,#6b6f86 50%,#6a6a5a 62%,#5a6a32 72%,#4a4a26 84%,#2e2a1c 100%)}
.cover-top{top:662px;font-style:italic;font-weight:800;font-size:26px;letter-spacing:.5px;color:#fff;text-shadow:0 2px 4px rgba(0,0,0,.5)}
.cover-mid{top:696px;font-family:'Archivo Black',sans-serif;font-size:48px;line-height:52px;color:var(--gold);text-shadow:0 3px 6px rgba(0,0,0,.5)}
.cover-from{top:748px;font-family:'Archivo Black',sans-serif;font-size:48px;line-height:52px;color:var(--gold);text-shadow:0 3px 6px rgba(0,0,0,.5)}
.cover-big{top:800px;font-family:'Archivo Black',sans-serif;font-size:142px;line-height:150px;color:var(--gold);text-shadow:0 4px 8px rgba(0,0,0,.55)}
.tag-small{top:968px;font-size:23px;font-weight:500;letter-spacing:1px}
.tag-big{top:996px;font-size:38px;font-weight:800}
.cover-web{top:1048px;font-size:21px;letter-spacing:2px;color:var(--gold)}

/* why panel */
.why-art{position:absolute;inset:0;background:linear-gradient(180deg,#4f8fb4 0%,#9cc0d6 16%,#e8c9a6 32%,#f0b48a 40%,#c8d3df 55%,#b9cfe0 72%,#8a9a6a 86%,#5e6a38 100%)}
.why-title{position:absolute;left:50px;top:64px;font-family:'Archivo Black',sans-serif;font-size:40px;line-height:40px;color:var(--ink-teal)}
.ask{position:absolute;left:49px;width:409px;height:76px;border-radius:38px;display:flex;align-items:center;padding-left:66px;font-weight:700;font-size:16px;line-height:19px}
.ask--one{top:150px;background:rgba(170,148,104,.9)}
.ask--two{top:248px;background:rgba(54,136,140,.88)}
.ask__icon{position:absolute;left:14px;top:16px;font-family:'Archivo Black',sans-serif;font-size:42px;line-height:44px;color:#fff}
.why-body{position:absolute;left:55px;width:410px;top:348px;font-size:17px;line-height:20px;font-weight:500;color:#1d2a30}
.verse-card{position:absolute;left:54px;width:423px;border-radius:26px;background:rgba(255,255,255,.38);padding:50px 42px 0 42px;font-size:17px;line-height:20px;color:#1f2c33}
.verse-card--a{top:456px;height:185px}
.verse-card--b{top:690px;height:194px}
.verse-ref{display:block;margin-top:14px;font-weight:700}
.verse-card .qmark{font-size:86px;color:#2a6a80}
.q-open{left:8px;top:-30px}
.q-close{right:20px;bottom:-48px}

/* way panel */
.way-script{top:42px;font-size:62px;color:#fff;padding-left:30px}
.way-title{top:108px;font-family:'Archivo Black',sans-serif;font-size:40px;color:var(--gold)}
.step-card{position:absolute;left:85px;width:379px;border-radius:26px;text-align:center;padding:44px 30px 0;font-size:15px;line-height:18px}
.step-card .verse-ref{margin-top:8px}
.step-card .qmark{font-size:48px;color:#c9dfe3}
.step-card .q-open{left:18px;top:-10px}
.step-card .q-close{right:0;bottom:-30px}
.step-card--one{top:185px;height:156px;background:rgba(110,150,110,.7)}
.step-card--one .verse-ref{color:var(--gold)}
.step-card--two{top:365px;height:152px;background:rgba(44,104,124,.85)}
.step-card--two .verse-ref{color:var(--lbl-cyan)}
.step-card--three{top:541px;height:159px;background:rgba(76,136,40,.9)}
.step-card--three .verse-ref{color:var(--lbl-lime)}
.step-card--four{top:727px;height:152px;background:rgba(44,96,120,.85)}
.step-card--four .verse-ref{color:#3ab0f0}
.prayer{top:928px;left:80px;right:80px;font-size:16px;line-height:19.5px}
</style>
</head>
<body>

<section class="spread spread--outside">
  <div class="panel panel--back">
    <h2 class="abs journey-title">YOUR<br>JOURNEY</h2>
    <p class="abs journey-sub">CONTINUES</p>
    <p class="abs script congrats">Congratulations!</p>
    <p class="abs lead">If you have accepted Jesus as your Savior,<br>you are now on the path to heaven.<br>What's next?</p>

    <div class="step step--bible"><span class="step__label">READ THE BIBLE</span><p class="step__text">Start with the book of John to learn<br>more about Jesus.</p></div>
    <div class="step step--pray"><span class="step__label">PRAY DAILY</span><p class="step__text">Talk to God as you would a friend</p></div>
    <div class="step step--church"><span class="step__label">FIND A CHURCH</span><p class="step__text">Join a community of believers who can<br>support and guide you.</p></div>
    <div class="step step--share"><span class="step__label">SHARE THE GOOD NEWS</span><p class="step__text">Talk to God as you would a friend</p></div>

    <p class="abs contact-intro">If you have questions or want more<br>resources, reach out to us at</p>
    <div class="abs contact-icons">
      <span class="rule"></span>
      <span class="icon-dot"><svg width="12" height="14" viewBox="0 0 12 14"><path d="M6 0a5 5 0 0 0-5 5c0 4 5 9 5 9s5-5 5-9a5 5 0 0 0-5-5zm0 7a2 2 0 1 1 0-4 2 2 0 0 1 0 4z" fill="#1d4a58"/></svg></span>
      <span class="icon-dot"><svg width="12" height="12" viewBox="0 0 12 12"><path d="M2.5 0.5l2 2.5-1.2 1.4a7 7 0 0 0 4.3 4.3L9 7.5l2.5 2-1 2C5 11.5.5 7 .5 1.5z" fill="#1d4a58"/></svg></span>
      <span class="icon-dot"><svg width="13" height="10" viewBox="0 0 13 10"><rect x=".5" y=".5" width="12" height="9" rx="1" fill="#1d4a58"/><path d="M1 1l5.5 4.5L12 1" stroke="#b9d46a" fill="none"/></svg></span>
      <span class="icon-dot"><svg width="13" height="13" viewBox="0 0 13 13"><circle cx="6.5" cy="6.5" r="5.8" fill="none" stroke="#1d4a58" stroke-width="1.3"/><ellipse cx="6.5" cy="6.5" rx="2.5" ry="5.8" fill="none" stroke="#1d4a58" stroke-width="1.1"/><path d="M.7 6.5h11.6" stroke="#1d4a58" stroke-width="1.1"/></svg></span>
      <span class="rule"></span>
    </div>
    <p class="abs address">3403 lorem ipsum<br>Maple Hollow, ST 40210<br>City: lorem ipsum<br>State: lorem ipsum<br>Zip:123445</p>
    <p class="abs phone">555 0142 7788</p>
    <p class="abs email">hello@lanterntrail.org</p>
    <p class="abs web">www.lanterntrail.org</p>
    <p class="abs closing"><span class="qmark" style="left:84px;top:-14px">“</span>I have come that they may have life, and<br>have it to the full<span class="qmark" style="right:84px;top:0">”</span></p>
  </div>

  <div class="panel panel--cover">
    <div class="cover-art" role="img" aria-label="Photo of a long stairway rising through glowing clouds to a bright sky, with a winding dirt road through Iowa farm fields and grass in the foreground"></div>
    <p class="abs cover-top">A LANTERN TRAIL TOWARD</p>
    <p class="abs cover-mid">BRIGHT SKIES</p>
    <p class="abs cover-from">FROM</p>
    <h1 class="abs cover-big">IOWA</h1>
    <p class="abs tag-small">THE ROAD STARTS RIGHT</p>
    <p class="abs tag-big">WHERE YOU ARE</p>
    <p class="abs cover-web">www.lanterntrail.org</p>
  </div>
</section>

<section class="spread spread--inside">
  <div class="panel panel--why">
    <div class="why-art" role="img" aria-label="Photo of a sunset sky with soft clouds above a row of autumn trees"></div>
    <h2 class="why-title">WHY ASK<br>ABOUT HEAVEN?</h2>
    <div class="ask ask--one"><span class="ask__icon">?</span>Many people wonder about life after<br>death. Is there a heaven?</div>
    <div class="ask ask--two"><span class="ask__icon">?</span>How can you be sure you'll<br>get there?</div>
    <p class="why-body">The good news is that God has provided clear answers in the Bible. Heaven is not just a destination; it's a promise for those who choose the right path.</p>
    <div class="verse-card verse-card--a"><span class="qmark q-open">“</span>For God so loved the world that he gave his one and only Son, that whoever believes in him shall not perish but have eternal life<span class="verse-ref">John 3:16</span><span class="qmark q-close">”</span></div>
    <div class="verse-card verse-card--b"><span class="qmark q-open">“</span>Jesus answered, 'I am the way and the truth and the life. No one comes to the Father except through me.<span class="verse-ref">John 14:6</span><span class="qmark q-close">”</span></div>
  </div>

  <div class="panel panel--way">
    <p class="abs script way-script">The Way</p>
    <h2 class="abs way-title">TO HEAVEN</h2>
    <div class="step-card step-card--one"><span class="qmark q-open">“</span>Acknowledge Your NeedWe all fall short of God's perfect standard. "For all have sinned and fall short of the glory of God<span class="verse-ref">Romans 3:23</span><span class="qmark q-close">”</span></div>
    <div class="step-card step-card--two"><span class="qmark q-open">“</span>Believe in Jesus ChristJesus died on the cross to take the punishment for your sins. "But God demonstrates his own love for us in this: While we were still sinners, Christ died for us."<span class="verse-ref">Romans 5:8</span><span class="qmark q-close">”</span></div>
    <div class="step-card step-card--three"><span class="qmark q-open">“</span>Accept God's Gift of SalvationEternal life is a free gift, not something you can earn. "For it is by grace you have been saved, through faith and this is not from yourselves, it is the gift of God<span class="verse-ref">Ephesians 2:8–9</span><span class="qmark q-close">”</span></div>
    <div class="step-card step-card--four"><span class="qmark q-open">“</span>Confess and CommitPray and invite Jesus into your life as your Savior. "If you declare with your mouth, 'Jesus is Lord,' and believe in your heart that God raised him from the dead, you will be saved<span class="verse-ref">Romans 10:9</span><span class="qmark q-close">”</span></div>
    <p class="abs prayer">Dear God, I know I have sinned and need your forgiveness. I believe Jesus died for my sins and rose from the dead. I trust Him as my Savior and commit my life to Him. Thank you for your grace and the gift of eternal life. Amen</p>
  </div>
</section>

</body>
</html>
```